Tuition Center Website

We need a new web site for a tutoring company based in sydney.

We only teach senior highschool students and pride ourselves on building the students abilities to think their way through life.

I would like a bright and vibrant website that looks professional and modern.
It needs to look simple and neat but also have the functionality we need.
Images and flash would be good.

Please keep in mind that the site must be appealing to a younger audience.

We need a multipage website with the following navigation bars:

1.Home (As logo not "home" button)
I would like a news box/ticker somewhere that can stream our chatterbook and pipstream feeds and also any news updates we want to put up.
Subscribe to newsletter button.

2. About us.
This needs to be a pull down into:
-What we do
-Why we do it
-How we do it

3. Courses
Pulldown into:
-Maths
-English
-Science
(we may need to attach extra pages behind these e.g. Courses/Science/Physics or Courses/Science/Chemistry and possibly add a link to a new zandlo form)

4. Inspired
This page is like a blog page where we can upload videos, links to articles that we find to be inspiring and hopefully will inspire others.

5. Inspire
This is a recruitment page. Only content here.

6. Contact us.
Mapquill map widget and a 'contact us' form

* Our branding requires green close to #12FF3D

***Please have a look at the current website.
@ www.velmorlearning.com.au

Thanks everybody hope the revision of my brief is better and more informative than my last one

Target Market(s)

senior highschool students aged 15-19, parents ( to a lesser degree)

Industry/Entity Type

It Company

Requirements
Must have
• Ability to change content on pages.

The green doesn't have to be everywhere, but it must be obvious that it is our colour.

Nice to have
• Sites with a nicer mix of images and flash will be given more consideration. But then again, if you amaze us, you amaze us and we will go with your design.
Should not have
• Should stay away from ocre, brown colours and serif fonts.

```html
<!DOCTYPE html>
<html lang="en">
<head>
<meta charset="utf-8">
<title>velmor learning – HSC coaching</title>
<link href="https://fonts.googleapis.com/css2?family=Arimo:ital,wght@0,400;0,700;1,400&display=swap" rel="stylesheet">
<style>
:root{
  --green:#75b318;
  --green-dark:#4e8f0b;
  --green-bright:#8cc63f;
  --ink:#333;
  --text:#666;
  --muted:#999;
  --panel:#f1f1f1;
  --nav:#4a4a4a;
  --footer:#3a3a3a;
}
*{box-sizing:border-box;margin:0;padding:0}
html,body{width:862px;height:1200px;overflow:hidden}
body{font-family:"Arimo",Arial,sans-serif;color:var(--text);background:#fff}
a{text-decoration:none;color:inherit}
.page{position:relative;width:862px;height:1200px;overflow:hidden;background:linear-gradient(#e6e6e6,#f6f6f6 40%,#eeeeee)}
.abs{position:absolute}
.topband{left:0;top:0;width:862px;height:173px;background:var(--green)}
.toplinks{right:118px;top:12px;font-size:10px;color:#fff;white-space:nowrap}
.toplinks span{margin:0 5px}
.like{left:748px;top:10px;height:16px;padding:0 4px;background:#eef0f4;border:1px solid #c9ccd3;border-radius:2px;font-size:8px;line-height:14px;color:#4a5a80;white-space:nowrap}
.likecount{left:805px;top:10px;height:16px;padding:0 3px;background:#fff;border:1px solid #ccc;border-radius:2px;font-size:8px;line-height:14px;color:#333}
.sheet{left:64px;top:35px;width:734px;height:1091px;background:#fff}
.home-logo{left:74px;top:48px;width:130px;height:120px;display:block}
.brand-mark{position:absolute;left:10px;top:2px;width:86px;height:76px;background:var(--green-bright)}
.brand-name{position:absolute;left:0;top:80px;font-size:20px;line-height:19px;font-weight:700;color:var(--green-dark)}
.newsletter{left:560px;top:51px;width:100px;height:21px;border-radius:3px;background:linear-gradient(#86c42a,#4e8f0b);color:#fff;font-size:8.5px;line-height:21px;text-align:center;white-space:nowrap}
.search{left:670px;top:51px;width:120px;height:21px;border:1px solid #ccc;background:linear-gradient(#fff,#f1f1f1);font-size:8.5px;line-height:19px;padding-left:9px;color:#555}
.search svg{position:absolute;right:6px;top:4px}
.contact{right:70px;font-size:10px;font-weight:700;color:var(--ink);text-align:right;white-space:nowrap}
.contact b{color:var(--green-dark)}
.nav{left:242px;top:126px;width:550px;height:42px;display:flex;background:linear-gradient(#5a5a5a,#3e3e3e)}
.nav a{display:block;width:110px;height:42px;line-height:42px;font-size:10.5px;color:#fff;text-align:center;border-right:1px solid #2e2e2e;border-left:1px solid #666}
.nav a.active{background:linear-gradient(#6fb21b,#3f8a0b);border-color:#3f8a0b}
.slider{left:70px;top:176px;width:722px;height:194px;background:#e6e6e6;padding:4px}
.slide{position:relative;width:714px;height:186px;background:linear-gradient(90deg,#fafafa,#f3f3f3 60%,#ececec);border:1px solid #d4d4d4}
.slide h1{position:absolute;left:31px;top:25px;font-size:26px;font-weight:400;color:var(--ink);letter-spacing:.3px}
.slide h2{position:absolute;left:29px;top:59px;font-size:12.5px;font-weight:400;color:var(--green-dark)}
.slide p{position:absolute;left:29px;top:82px;width:400px;font-size:9.4px;line-height:16.5px;color:var(--text)}
.btn{display:inline-block;background:linear-gradient(#666,#3a3a3a);color:#fff;font-size:10.5px;border-radius:3px;text-align:center;box-shadow:0 1px 2px rgba(0,0,0,.4)}
.slide .btn{position:absolute;left:29px;top:138px;width:88px;height:24px;line-height:24px}
.hero-photo{position:absolute;left:436px;top:4px;width:276px;height:180px;background:radial-gradient(circle at 60% 40%,#d9a489,#b57862 30%,#9fb0c8 55%,#e8ecef 75%)}
.arrow{width:22px;height:22px;border-radius:50%;background:#fff;border:1px solid #bbb;box-shadow:0 1px 2px rgba(0,0,0,.3)}
.arrow svg{display:block;margin:5px auto}
.section-title{font-size:15px;color:var(--green-dark);font-weight:400}
.quote{left:70px;width:192px;height:76px;border:3px solid #e4e4e4;border-radius:6px;background:#fff;padding:6px 8px 0 9px;font-size:8.5px;line-height:15px;font-style:italic;color:var(--muted);text-align:justify}
.quote::after{content:"";position:absolute;right:22px;bottom:-17px;border-left:22px solid transparent;border-top:15px solid #e4e4e4}
.quote b{font-size:13px;color:#777;font-style:normal;line-height:8px}
.by{left:100px;font-size:10px;font-style:italic;color:var(--green-dark)}
.by small{font-size:8.5px;color:#555;margin-left:4px}
.more{left:70px;width:192px;height:23px;background:var(--panel);font-size:10px;line-height:23px;text-align:center;color:#777}
.news-thumb{left:72px;width:75px;height:52px}
.news-text{left:155px;width:106px;font-size:10px;line-height:12px;color:#555;text-align:justify}
.news-text small{display:block;font-size:8px;color:#aaa;margin-top:4px}
.trial{left:70px;top:932px;width:192px;height:182px;border:3px solid #d2d2d2;border-radius:5px;background:#fff;box-shadow:0 0 0 1px #aaa}
.trial-head{position:absolute;left:6px;top:8px;width:175px;height:65px;background:var(--green-bright)}
.trial-head .sq{position:absolute;left:8px;top:6px;width:36px;height:30px;background:#fff}
.trial-head .nm{position:absolute;left:6px;top:40px;font-size:10px;font-weight:700;color:#fff;line-height:10px}
.trial-head .ask{position:absolute;right:8px;top:4px;text-align:right;font-size:15.5px;font-weight:700;color:#fff;line-height:19px}
.trial p{position:absolute;left:10px;top:84px;width:166px;font-size:9.5px;line-height:15px;color:#555;text-align:justify}
.trial .btn{position:absolute;left:43px;top:135px;width:87px;height:24px;line-height:24px}
.post{left:274px;width:518px;height:169px;background:var(--panel);border-radius:3px}
.post .img{position:absolute;left:10px;top:10px;width:166px;height:146px;border:4px solid #e2e2e2;border-radius:3px}
.post h3{position:absolute;left:192px;top:19px;font-size:11.6px;font-weight:400;color:var(--green-dark)}
.post p{position:absolute;left:192px;top:40px;width:292px;font-size:10px;line-height:16.6px;color:#666;text-align:justify}
.post .meta{position:absolute;left:193px;top:130px;width:288px;height:26px;background:#e5e5e5;border-radius:4px;font-size:9px;line-height:26px;color:#333;padding-left:12px;white-space:nowrap}
.post .meta span{margin:0 9px}
.share{position:absolute;left:494px;top:0;width:24px;height:169px;background:#e8e8e8;border-radius:0 3px 3px 0}
.share i{position:absolute;left:8px;width:9px;height:9px;border-radius:2px;background:#3a7fc0}
.footer{left:0;top:1126px;width:862px;height:74px;background:var(--footer)}
.footlinks{left:64px;top:1144px;font-size:9.6px;color:#ddd;white-space:nowrap}
.footlinks span{margin:0 6px;color:#aaa}
.copy{left:64px;top:1168px;font-size:9.6px;color:#ddd;white-space:nowrap}
.dot{width:18px;height:18px;border-radius:50%;background:var(--green)}
</style>
</head>
<body>
<div class="page">
  <div class="abs topband"></div>
  <div class="abs toplinks">Studies Board Past HSC Papers<span>|</span>State Students Online<span>|</span>Uni Entry Centre<span>|</span>State HSC Online [Study Resources]<span>|</span>Help for Study Stress<span>|</span></div>
  <div class="abs like">chatterbook</div>
  <div class="abs likecount">3k</div>

  <div class="abs sheet"></div>

  <a class="abs home-logo" href="#" aria-label="velmor learning home">
    <span class="brand-mark"></span>
    <span class="brand-name">velmor<br>learning</span>
  </a>

  <a class="abs newsletter" href="#">Subscribe to newsletter</a>
  <div class="abs search">Search
    <svg width="11" height="11" viewBox="0 0 11 11"><circle cx="4.5" cy="4.5" r="3.3" fill="none" stroke="#222" stroke-width="1.6"/><path d="M7 7l3 3" stroke="#222" stroke-width="2"/></svg>
  </div>
  <div class="abs contact" style="top:86px">Street: 48 Kestrel Pde Ashgrove NSW 2199</div>
  <div class="abs contact" style="top:103px">Phone: <b>(02) 5550 1482</b> &nbsp;|&nbsp; Email: <b>learn@velmorlearning.com.au</b></div>

  <nav class="abs nav">
    <a href="#">About Us</a>
    <a href="#">Courses</a>
    <a href="#">Inspired</a>
    <a href="#">Inspire</a>
    <a href="#">Contact Us</a>
  </nav>

  <section class="abs slider">
    <div class="slide">
      <h1>i am velmor.</h1>
      <h2>real HSC coaching &amp; mentoring.</h2>
      <p>The HSC help you need, in the years you need it. We offer small classes, individualised attention and genuine care for each student. It's different - in a good way. Feel free to find out more about us, and let us know if there's any way we can help you on your journey.</p>
      <span class="btn">ENQUIRE NOW</span>
      <div class="hero-photo" role="img" aria-label="Photo of a student lying on the floor working on a laptop"></div>
    </div>
  </section>
  <div class="abs arrow" style="left:59px;top:262px"><svg width="8" height="10" viewBox="0 0 8 10"><path d="M6 1L2 5l4 4" fill="none" stroke="#333" stroke-width="2"/></svg></div>
  <div class="abs arrow" style="left:779px;top:262px"><svg width="8" height="10" viewBox="0 0 8 10"><path d="M2 1l4 4-4 4" fill="none" stroke="#333" stroke-width="2"/></svg></div>

  <h2 class="abs section-title" style="left:71px;top:386px">What Our Students Say</h2>
  <div class="abs quote" style="top:414px"><b>“</b> I like the support the most, how the people and teachers here pick you off your feet, make you do better and tell you that it's not the end of the world!! <b>”</b></div>
  <div class="abs by" style="top:500px">~Maribel,<small>Ashgrove Girls HS</small></div>
  <div class="abs quote" style="top:522px"><b>“</b> I like the support the most, how the people and teachers here pick you off your feet, make you do better and tell you that it's not the end of the world!! <b>”</b></div>
  <div class="abs by" style="top:608px">~Maribel,<small>Ashgrove Girls HS</small></div>
  <div class="abs more" style="top:633px">VIEW MORE</div>

  <h2 class="abs section-title" style="left:71px;top:672px">Recent News</h2>
  <div class="abs news-thumb" style="top:703px;background:linear-gradient(135deg,#8a5a3a,#c98d5a 50%,#e7d9c4)" role="img" aria-label="Photo of a student reading in a library"></div>
  <div class="abs news-text" style="top:704px">Suspendisse bibendum ornare tortor dignissim sit amet.<small>Mar-29-2013</small></div>
  <div class="abs news-thumb" style="top:770px;background:linear-gradient(135deg,#6b3b2a,#c4876a 50%,#3f6a4a)" role="img" aria-label="Photo of students studying together at a table"></div>
  <div class="abs news-text" style="top:771px">Suspendisse bibendum ornare tortor dignissim sit amet.<small>Mar-29-2013</small></div>
  <div class="abs news-thumb" style="top:837px;background:linear-gradient(135deg,#2f3a4a,#a3c06a 45%,#e6e2dc)" role="img" aria-label="Photo of students in a classroom"></div>
  <div class="abs news-text" style="top:838px">Suspendisse bibendum ornare tortor dignissim sit amet.<small>Mar-29-2013</small></div>
  <div class="abs more" style="top:898px">VIEW MORE</div>

  <aside class="abs trial">
    <div class="trial-head"><div class="sq"></div><div class="nm">velmor<br>learning</div><div class="ask">Ask for your<br>free trial<br>lesson.</div></div>
    <p>Because we believe you shouldn't have to sign up until you see what it's actually like. Call or email us now!</p>
    <span class="btn">ENQUIRE NOW</span>
  </aside>

  <h2 class="abs section-title" style="left:274px;top:386px">Latest Blog</h2>

  <article class="abs post" style="top:414px">
    <div class="img" style="background:linear-gradient(135deg,#3a2a22,#b58a6f 45%,#e9e4dc)" role="img" aria-label="Photo of students writing in a classroom"></div>
    <h3>Phasellus ac ligula sit amet velit vulputate egestas.</h3>
    <p>Suspendisse bibendum ullamcorper eros, in ornare tortor dignissim sit amet. Integer mauris odio, feugiat nec lobortis vel, accumsan eu lacus. Aliquam vestibulum facilisis sem, non condimentum urna mattis at. Pel lentesque at enim at lorem posuere adipiscing. Mauris enim nibh, ultrices ut accumsan vitae.</p>
    <div class="meta">Posted on : March 29, 2013<span>|</span>10.15 A.M<span>|</span>View more</div>
    <div class="share"><i style="top:70px"></i><i style="top:86px"></i><i style="top:101px"></i><i style="top:117px;background:#d9452f"></i><i style="top:132px;background:#c8232c"></i><i style="top:147px;background:#1c6fa8"></i></div>
  </article>

  <article class="abs post" style="top:591px">
    <div class="img" style="background:linear-gradient(135deg,#5a3f3a,#3a2a45 45%,#c9b5a5)" role="img" aria-label="Photo of students raising hands in class"></div>
    <h3>Phasellus ac ligula sit amet velit vulputate egestas.</h3>
    <p>Suspendisse bibendum ullamcorper eros, in ornare tortor dignissim sit amet. Integer mauris odio, feugiat nec lobortis vel, accumsan eu lacus. Aliquam vestibulum facilisis sem, non condimentum urna mattis at. Pel lentesque at enim at lorem posuere adipiscing. Mauris enim nibh, ultrices ut accumsan vitae.</p>
    <div class="meta">Posted on : March 29, 2013<span>|</span>10.15 A.M<span>|</span>View more</div>
    <div class="share"><i style="top:70px"></i><i style="top:86px"></i><i style="top:101px"></i><i style="top:117px;background:#d9452f"></i><i style="top:132px;background:#c8232c"></i><i style="top:147px;background:#1c6fa8"></i></div>
  </article>

  <article class="abs post" style="top:769px">
    <div class="img" style="background:linear-gradient(135deg,#c9a06a,#e9d7b8 40%,#3f6e9a)" role="img" aria-label="Photo of students taking an exam"></div>
    <h3>Phasellus ac ligula sit amet velit vulputate egestas.</h3>
    <p>Suspendisse bibendum ullamcorper eros, in ornare tortor dignissim sit amet. Integer mauris odio, feugiat nec lobortis vel, accumsan eu lacus. Aliquam vestibulum facilisis sem, non condimentum urna mattis at. Pel lentesque at enim at lorem posuere adipiscing. Mauris enim nibh, ultrices ut accumsan vitae.</p>
    <div class="meta">Posted on : March 29, 2013<span>|</span>10.15 A.M<span>|</span>View more</div>
    <div class="share"><i style="top:70px"></i><i style="top:86px"></i><i style="top:101px"></i><i style="top:117px;background:#d9452f"></i><i style="top:132px;background:#c8232c"></i><i style="top:147px;background:#1c6fa8"></i></div>
  </article>

  <article class="abs post" style="top:946px">
    <div class="img" style="background:linear-gradient(135deg,#4a3a30,#c2957a 45%,#ece8e2)" role="img" aria-label="Photo of a student writing notes"></div>
    <h3>Phasellus ac ligula sit amet velit vulputate egestas.</h3>
    <p>Suspendisse bibendum ullamcorper eros, in ornare tortor dignissim sit amet. Integer mauris odio, feugiat nec lobortis vel, accumsan eu lacus. Aliquam vestibulum facilisis sem, non condimentum urna mattis at. Pel lentesque at enim at lorem posuere adipiscing. Mauris enim nibh, ultrices ut accumsan vitae.</p>
    <div class="meta">Posted on : March 29, 2013<span>|</span>10.15 A.M<span>|</span>View more</div>
    <div class="share"><i style="top:70px"></i><i style="top:86px"></i><i style="top:101px"></i><i style="top:117px;background:#d9452f"></i><i style="top:132px;background:#c8232c"></i><i style="top:147px;background:#1c6fa8"></i></div>
  </article>

  <footer class="abs footer"></footer>
  <div class="abs footlinks">About Us<span>|</span>Courses<span>|</span>Inspired<span>|</span>Inspire<span>|</span>Contact Us</div>
  <div class="abs copy">Copyright &nbsp;©&nbsp; 2013 &nbsp;&nbsp; www.velmorlearning.com.au &nbsp;&nbsp; All rights reserved.</div>
  <div class="abs dot" style="left:705px;top:1153px"></div>
  <div class="abs dot" style="left:730px;top:1153px"></div>
  <div class="abs dot" style="left:756px;top:1153px"></div>
  <div class="abs dot" style="left:781px;top:1153px"></div>
</div>
</body>
</html>
```